Home Remodeling company needs a business card design

we need a business card design for home remodeling company in hamilton county, indiana USA. we offers a wide range of construction services including whole house renovations, Design and Build Basements and Kitchen and Bathroom Remodeling . we would like to see designs for both site of business card that use the same color of the company logo and also including all information below :
1- Karim Feltous CEO / General Contractor
2- all company contacts Telephone numbers ( 1-888-DULOM-47 ) ( 317-555-0193) email address ( info@dulomhome.com) website ( www.dulomhome.com ) and social media logos (Facebook- twitter- google plus )
3- company logo
4- licensed . insured . bonded

```html
<!DOCTYPE html>
<html lang="en">
<head>
<meta charset="utf-8">
<title>Dulom Home Remodeling – Business Card</title>
<link rel="stylesheet" href="https://fonts.googleapis.com/css2?family=Source+Sans+3:wght@400;600;700&display=swap">
<style>
  :root {
    --backdrop: #2b2522;
    --card: #0e0e0f;
    --card-edge: #1a1a1b;
    --name-grey: #55555a;
    --accent-red: #d2323c;
    --text-white: #f2f2f2;
  }
  * { box-sizing: border-box; margin: 0; padding: 0; }
  html, body {
    width: 1200px; height: 844px; overflow: hidden;
    background: var(--backdrop);
    font-family: "Source Sans 3", "Helvetica Neue", Arial, sans-serif;
  }
  .stage {
    position: relative; width: 1200px; height: 844px;
    display: flex; align-items: center; justify-content: center; gap: 60px;
  }
  .card {
    position: relative; width: 520px; height: 297px;
    background: linear-gradient(160deg, #141415, var(--card));
    border: 1px solid var(--card-edge);
    box-shadow: 0 14px 30px rgba(0,0,0,.45);
  }
  .company {
    display: flex; align-items: center; gap: 10px;
  }
  .company-square {
    width: 12px; height: 12px; background: var(--accent-red); flex: none;
  }
  .company-name {
    font-size: 30px; font-weight: 700; color: var(--name-grey);
    line-height: 1; white-space: nowrap;
  }

  /* front */
  .card-front .company { position: absolute; left: 52px; top: 62px; }
  .contact-list {
    position: absolute; right: 34px; top: 120px;
    list-style: none; text-align: right;
    color: var(--text-white); font-size: 14px; line-height: 22px;
  }
  .contact-list li { display: flex; justify-content: flex-end; align-items: center; gap: 8px; }
  .contact-list svg { width: 11px; height: 11px; fill: var(--accent-red); flex: none; }
  .person { position: absolute; left: 52px; top: 198px; }
  .person-name { color: var(--accent-red); font-size: 19px; font-weight: 600; }
  .person-title { color: var(--text-white); font-size: 14px; margin-top: 1px; }
  .social-row { position: absolute; left: 52px; top: 254px; display: flex; gap: 12px; }
  .social-dot {
    width: 24px; height: 24px; border-radius: 50%;
    background: var(--text-white); border: 2px solid #2a2a2a;
  }

  /* back */
  .card-back .company-block {
    position: absolute; left: 0; right: 0; top: 112px;
    display: flex; flex-direction: column; align-items: center;
  }
  .credentials {
    color: var(--accent-red); font-size: 16px; font-weight: 600;
    margin-top: 14px;
  }
</style>
</head>
<body>
<main class="stage">
  <section class="card card-front" aria-label="Business card front">
    <div class="company">
      <span class="company-square"></span>
      <span class="company-name">Dulom Home Remodeling</span>
    </div>

    <ul class="contact-list">
      <li>1-888-DULOM-47
        <svg viewBox="0 0 24 24" aria-hidden="true"><path d="M6.6 10.8a15.1 15.1 0 0 0 6.6 6.6l2.2-2.2c.3-.3.7-.4 1-.2 1.1.4 2.3.6 3.6.6.6 0 1 .4 1 1V20c0 .6-.4 1-1 1A17 17 0 0 1 3 4c0-.6.4-1 1-1h3.5c.6 0 1 .4 1 1 0 1.3.2 2.5.6 3.6.1.3 0 .7-.2 1z"/></svg>
      </li>
      <li>317-555-0193
        <svg viewBox="0 0 24 24" aria-hidden="true"><path d="M6.6 10.8a15.1 15.1 0 0 0 6.6 6.6l2.2-2.2c.3-.3.7-.4 1-.2 1.1.4 2.3.6 3.6.6.6 0 1 .4 1 1V20c0 .6-.4 1-1 1A17 17 0 0 1 3 4c0-.6.4-1 1-1h3.5c.6 0 1 .4 1 1 0 1.3.2 2.5.6 3.6.1.3 0 .7-.2 1z"/></svg>
      </li>
      <li>info@dulomhome.com
        <svg viewBox="0 0 24 24" aria-hidden="true"><path d="M2 5h20v14H2z M3 6l9 7 9-7" stroke="#0e0e0f" stroke-width="1.5"/></svg>
      </li>
      <li>www.dulomhome.com
        <svg viewBox="0 0 24 24" aria-hidden="true"><path d="M10 14a4 4 0 0 0 5.7 0l4-4a4 4 0 0 0-5.7-5.7l-1.5 1.5 1.4 1.4 1.5-1.5a2 2 0 0 1 2.9 2.9l-4 4a2 2 0 0 1-2.9 0zM14 10a4 4 0 0 0-5.7 0l-4 4A4 4 0 0 0 10 19.7l1.5-1.5-1.4-1.4-1.5 1.5a2 2 0 0 1-2.9-2.9l4-4a2 2 0 0 1 2.9 0z"/></svg>
      </li>
    </ul>

    <div class="person">
      <p class="person-name">Karim Feltous</p>
      <p class="person-title">CEO / General Contractor</p>
    </div>

    <div class="social-row" aria-label="Social media links">
      <span class="social-dot"></span>
      <span class="social-dot"></span>
      <span class="social-dot"></span>
    </div>
  </section>

  <section class="card card-back" aria-label="Business card back">
    <div class="company-block">
      <div class="company">
        <span class="company-square"></span>
        <span class="company-name">Dulom Home Remodeling</span>
      </div>
      <p class="credentials">Licensed . Insured . Bonded</p>
    </div>
  </section>
</main>
</body>
</html>
```